Business Cards for Internet Security Company

Awesome designers! This is the opportunity to help design cards for a forward thinking network security company. They use threat information gathered from peer groups to make intelligent decisions on what threats are relevant and which arent. ( not that you need this to do designs, but just so you know where they are coming from. ) :-)

We'd like to see a two side design and the deliverables will be in illustrator 4. The logo is attached and the logo colors are attached in the JPG and I've attached a an eps of the logo and icon

Security

```html
<!DOCTYPE html>
<html lang="en">
<head>
<meta charset="utf-8">
<title>Kestrelon Business Card</title>
<link rel="stylesheet" href="https://fonts.googleapis.com/css2?family=Exo+2:wght@400;500;600&display=swap">
<style>
  :root {
    --page-bg: #e9ebee;
    --card-white: #ffffff;
    --card-shade: #f1f2f4;
    --brand-navy: #175592;
    --brand-sky: #2f9fe2;
    --brand-sky-light: #6cc2f0;
    --logo-blue: #2b7cc2;
    --text-light: #ffffff;
  }
  * { box-sizing: border-box; margin: 0; padding: 0; }
  html, body { width: 1200px; height: 870px; overflow: hidden; }
  body {
    background: var(--page-bg);
    font-family: "Exo 2", sans-serif;
    position: relative;
  }
  .card {
    position: absolute;
    left: 250px;
    width: 700px;
    height: 400px;
    background: var(--card-white);
    box-shadow: 0 6px 18px rgba(0,0,0,0.12);
    overflow: hidden;
  }
  .card--front { top: 25px; }
  .card--back {
    top: 445px;
    background: linear-gradient(135deg, var(--card-white), var(--card-shade));
  }
  .card__shapes {
    position: absolute;
    inset: 0;
    width: 100%;
    height: 100%;
  }
  .brand {
    position: absolute;
    left: 30px;
    top: 176px;
    display: flex;
    align-items: center;
    gap: 12px;
  }
  .brand__dot {
    width: 40px;
    height: 40px;
    border-radius: 50%;
    background: var(--logo-blue);
  }
  .brand__name {
    font-size: 40px;
    font-weight: 500;
    color: var(--logo-blue);
    letter-spacing: 0.5px;
  }
  .contact {
    position: absolute;
    left: 372px;
    top: 34px;
    width: 290px;
    color: var(--text-light);
  }
  .contact__name {
    font-size: 24px;
    font-weight: 500;
    letter-spacing: 1.5px;
  }
  .contact__title {
    font-size: 15px;
    margin-top: 2px;
    letter-spacing: 0.5px;
  }
  .contact__address {
    margin-top: 56px;
    font-size: 15px;
    line-height: 1.35;
  }
  .contact__list {
    list-style: none;
    margin-top: 14px;
    font-size: 15px;
  }
  .contact__item {
    display: flex;
    justify-content: space-between;
    align-items: center;
    height: 26px;
  }
  .contact__item svg {
    width: 14px;
    height: 14px;
    fill: var(--text-light);
    stroke: var(--text-light);
  }
</style>
</head>
<body>

  <section class="card card--front" aria-label="Business card front">
    <svg class="card__shapes" viewBox="0 0 700 400" preserveAspectRatio="none" aria-hidden="true">
      <path d="M228 0 C 300 70, 330 230, 322 400 L700 400 L700 0 Z" fill="var(--brand-sky-light)"/>
      <path d="M242 0 C 318 70, 346 230, 338 400 L700 400 L700 0 Z" fill="var(--brand-sky)"/>
      <path d="M262 0 C 336 70, 362 230, 354 400 L700 400 L700 0 Z" fill="var(--brand-navy)"/>
    </svg>

    <div class="brand">
      <span class="brand__dot"></span>
      <span class="brand__name">Kestrelon</span>
    </div>

    <div class="contact">
      <p class="contact__name">MARCUS HALE</p>
      <p class="contact__title">Managing Director</p>
      <p class="contact__address">215 Calloway Street Suite 4,<br>Denford</p>
      <ul class="contact__list">
        <li class="contact__item">
          <span>012 555 0142</span>
          <svg viewBox="0 0 16 16" aria-label="Phone"><path stroke="none" d="M3 1l3 3-1.5 2a9 9 0 0 0 5.5 5.5L12 10l3 3-2 2C7 15 1 9 1 3z"/></svg>
        </li>
        <li class="contact__item">
          <span>012 555 0143</span>
          <svg viewBox="0 0 16 16" aria-label="Mobile"><rect x="4" y="1" width="8" height="14" rx="1.5" fill="none" stroke-width="1.5"/><circle cx="8" cy="12.5" r="0.9" stroke="none"/></svg>
        </li>
        <li class="contact__item">
          <span>012 555 0144</span>
          <svg viewBox="0 0 16 16" aria-label="Fax"><rect x="3" y="1" width="10" height="5" stroke="none"/><rect x="1" y="7" width="14" height="8" rx="1" stroke="none"/></svg>
        </li>
        <li class="contact__item">
          <span>hello@kestrelon.com</span>
          <svg viewBox="0 0 16 16" aria-label="Email"><rect x="1" y="3" width="14" height="10" fill="none" stroke-width="1.5"/><path d="M1 3l7 6 7-6" fill="none" stroke-width="1.5"/></svg>
        </li>
        <li class="contact__item">
          <span>www.kestrelon.com</span>
          <svg viewBox="0 0 16 16" aria-label="Website"><circle cx="8" cy="8" r="6.5" fill="none" stroke-width="1.4"/><ellipse cx="8" cy="8" rx="3" ry="6.5" fill="none" stroke-width="1.2"/><path d="M1.5 8h13" fill="none" stroke-width="1.2"/></svg>
        </li>
      </ul>
    </div>
  </section>

  <section class="card card--back" aria-label="Business card reverse"></section>

</body>
</html>
```